Harrowmere Freight, Project

Company Profile
Harrowmere Freight Sdn Bhd is a well established and experienced freight forwarder in Kuala Lumpur, Malaysia. We specialize in air and sea forwarding, Custom Brokerage and regulatory compliance services, inland transportation,
overseas freighting and warehousing and distribution management. With our dedicated qualified and experienced professionals, we are fully committed to serving our clients.

Our Mission
Based on the motto “Quick, Reliable and Polite”, Harrowmere Freight is dedicated to upholding the following three points corporate philosophy:
1. Adhering to the principle that “the customer always comes first”.
2. Contributing to the development of the local community.
3. Making it our duty to be responsible and sincere.

Our Edge
• One-Stop Logistics Solutions
• Extensive Network Throughout Malaysia
• Highly Qualified and Experienced Pool of Professionals
• Comprehensive IT Solutions
• Innovative and Customer-focused Solutions
• Flexible and Consistent in Managing Exceptions
• Total Supply Chain Visibility

Target Market(s)

We sell the logistics services to all the industry in Malaysia. (ONE Stop Logistics Solutions)

Industry/Entity Type

Logistic

Contact Information for Business Card

I want the back of the card to be white with the logo and slogan. i would like to see the logo on the front with the general info.

Requirements
Must have
• Name, Title, Office, Cell, Fax, Email, Address, Website
Nice to have
• Modern Design Business Card

```html
<!DOCTYPE html>
<html lang="en">
<head>
<meta charset="utf-8">
<title>Harrowmere Freight Stationery</title>
<link href="https://fonts.googleapis.com/css2?family=Questrial&display=swap" rel="stylesheet">
<style>
  :root{
    --bg:#ececec;
    --paper:#f6f6f6;
    --blue:#4f86c6;
    --blue-light:#6aa6da;
    --blue-dark:#4a79bd;
    --grey:#5f5f5f;
    --ink:#3c3c3c;
  }
  *{box-sizing:border-box;margin:0;padding:0}
  html,body{width:1200px;height:991px;overflow:hidden}
  body{background:var(--bg);font-family:"Questrial",sans-serif;color:var(--ink);position:relative}
  .sheet{position:absolute;background:var(--paper);box-shadow:0 2px 6px rgba(0,0,0,.18);overflow:hidden}
  .brand{font-family:"Questrial",sans-serif;color:var(--grey);white-space:nowrap;display:flex;align-items:center;gap:5px}
  .brand .dot{display:inline-block;border-radius:50%;background:var(--blue)}
  .band{position:absolute;left:0;bottom:0;width:100%}
  .band-url{position:absolute;bottom:3px;right:12px;color:#fff;letter-spacing:.2px;white-space:nowrap}
  .small{font-size:5.6px;line-height:7.2px}

  /* letterhead */
  .letterhead{left:71px;top:103px;width:397px;height:561px}
  .letterhead .brand{position:absolute;left:32px;top:72px;font-size:13px}
  .letterhead .brand .dot{width:8px;height:8px}
  .contact{position:absolute;left:295px;top:42px;color:#555}
  .contact li{list-style:none;display:flex;align-items:center;gap:3px}
  .contact .ic{display:inline-block;width:5px;height:5px;background:var(--blue);border-radius:1px}
  .letter-date{position:absolute;left:32px;top:133px}
  .recipient{position:absolute;left:32px;top:148px}
  .letter-body{position:absolute;left:32px;top:207px;width:334px;text-align:justify}
  .letter-body p{margin-bottom:6px;font-size:5.3px;line-height:6.9px}
  .salute{font-weight:bold;margin-bottom:8px!important}
  .signoff{position:absolute;left:32px;top:380px}
  .signature{position:absolute;left:85px;top:375px;width:60px;height:22px;background:linear-gradient(90deg,rgba(79,134,198,.12),rgba(79,134,198,.05));border-radius:3px}

  /* folder */
  .folder{left:507px;top:90px;width:432px;height:576px}
  .folder .spine{position:absolute;left:26px;top:0;width:1px;height:100%;background:rgba(0,0,0,.07)}
  .folder .brand{position:absolute;left:218px;top:126px;transform:translateX(-50%);font-size:22px}
  .folder .brand .dot{width:13px;height:13px}
  .pocket{position:absolute;left:0;top:214px;width:100%;height:362px}

  /* business cards */
  .card-front{left:66px;top:696px;width:171px;height:96px}
  .card-front .person{position:absolute;left:11px;top:12px;color:var(--blue-dark);font-size:5.6px;font-weight:bold;letter-spacing:.2px}
  .card-front .role{position:absolute;left:11px;top:19px;font-size:4.2px;color:#777}
  .card-front .brand{position:absolute;right:10px;top:30px;font-size:9px}
  .card-front .brand .dot{width:6px;height:6px}
  .card-front .details{position:absolute;left:11px;top:52px;font-size:3.8px;line-height:5px;color:#555;white-space:nowrap}
  .card-front .address{position:absolute;right:10px;top:72px;font-size:3.8px;line-height:5px;color:#555;text-align:right}
  .card-back{left:66px;top:810px;width:171px;height:94px}
  .card-back .brand{position:absolute;left:50%;top:38px;transform:translateX(-50%);font-size:10px}
  .card-back .brand .dot{width:6px;height:6px}
  .card-back .slogan{position:absolute;left:0;width:100%;top:54px;text-align:center;font-size:4.6px;color:var(--blue-dark);letter-spacing:.3px}

  /* compliment slip */
  .slip{left:266px;top:696px;width:416px;height:208px}
  .slip .brand{position:absolute;left:28px;top:68px;font-size:13px}
  .slip .brand .dot{width:8px;height:8px}
  .slip .addr{position:absolute;left:32px;top:98px;text-align:center;color:#666}

  /* envelope */
  .envelope{left:718px;top:696px;width:416px;height:208px}
  .flap{position:absolute;left:0;top:0;width:100%;height:60px}
  .envelope .flap-dot{position:absolute;left:50%;top:30px;transform:translate(-50%,-50%);width:10px;height:10px;border-radius:50%;background:#fff}
  .envelope .url{position:absolute;left:0;width:100%;top:181px;text-align:center;font-size:5.2px;color:#666}
</style>
</head>
<body>

<section class="sheet letterhead" aria-label="Letterhead">
  <div class="brand"><span class="dot"></span>Harrowmere Freight</div>
  <ul class="contact small">
    <li><span class="ic"></span>03 7781 2046</li>
    <li><span class="ic"></span>info@harrowmerefreight.com</li>
    <li><span class="ic"></span>www.harrowmerefreight.com</li>
    <li style="margin-top:3px">B12 Kelana Square, Jalan SS7,</li>
    <li>Petaling Jaya 47301</li>
  </ul>
  <p class="letter-date small">30.09.2015</p>
  <p class="recipient small">Recipient's name<br>Lindenweg 4<br>20095 Hamburg<br>Germany</p>
  <div class="letter-body">
    <p class="salute">Dear sir,</p>
    <p>Communication is a very integral part of living creatures, animals and humans. Communication may be verbal or written. Written communication however is only applicable to human beings. Can you even imagine a world without communication? Verbal communication can be through telephones, webcams or in person. Written communication is through letters, emails and mobile phone messages.</p>
    <p>In today's world of great inventions and technology, letters have somehow become redundant. It is the time for text messages or chats. But they still can communicate a lot more than all other modes of communication. Organizations and various government departments still bank on letters as a strong medium of communication. There is no comparison in costs of sending letters as compared to costs of mobile phone messages though – letters are far cheaper. Letters now commonly known as “hard copy documents” are considered more relevant and important than email copies of text messages as proof or evidence of some sort.</p>
    <p>Letters speak volumes about a person or an organization that writes it. So one must take utmost care ensuring that the language used in any letter is appropriate for the occasion for which it is being written. Since a letter is also a written proof or document, if there are certain things that should not form a part of it, then that too should be carefully handled.</p>
    <p>Writing a good letter is an art. But if for some reason someone is unable to write that perfect letter, these different types of letters provide a base for you to build on. Sample letters have been given for everyone to understand what all information needs to form a part of the letter type and then it can be customized.</p>
  </div>
  <p class="signoff small">Yours Sincerely,<br><b>Daniel Okoro</b></p>
  <div class="signature" role="img" aria-label="Handwritten signature"></div>
  <svg class="band" width="397" height="16" viewBox="0 0 397 16">
    <defs>
      <linearGradient id="lhGrey" x1="0" x2="1"><stop offset="0" stop-color="#555"/><stop offset="1" stop-color="#d0d0d0"/></linearGradient>
      <linearGradient id="lhBlue" x1="0" x2="1"><stop offset="0" stop-color="#5b95d2"/><stop offset="1" stop-color="#4c82c4"/></linearGradient>
    </defs>
    <polygon points="0,4 270,4 264,12 0,12" fill="url(#lhGrey)"/>
    <polygon points="274,0 397,0 397,16 0,16 0,13 266,13" fill="url(#lhBlue)"/>
  </svg>
  <span class="band-url small">WWW.HARROWMEREFREIGHT.COM</span>
</section>

<section class="sheet folder" aria-label="Presentation folder">
  <div class="spine"></div>
  <div class="brand"><span class="dot"></span>Harrowmere Freight</div>
  <svg class="pocket" width="432" height="362" viewBox="0 0 432 362">
    <defs>
      <linearGradient id="fdBlue" x1="0" y1="0" x2="0" y2="1"><stop offset="0" stop-color="#68a3d9"/><stop offset="1" stop-color="#4a79bd"/></linearGradient>
      <linearGradient id="fdGrey" x1="0" x2="1"><stop offset="0" stop-color="#c8c8c8"/><stop offset=".6" stop-color="#8a8a8a"/><stop offset="1" stop-color="#666"/></linearGradient>
    </defs>
    <polygon points="114,4 432,4 432,16 126,16" fill="url(#fdGrey)"/>
    <path d="M0,0 H106 Q110,0 113,4 L124,18 H432 V362 H0 Z" fill="url(#fdBlue)"/>
  </svg>
</section>

<section class="sheet card-front" aria-label="Business card front">
  <p class="person">NORA WHITFIELD</p>
  <p class="role">General Manager</p>
  <div class="brand"><span class="dot"></span>Harrowmere Freight</div>
  <p class="details">Office: 03 7781 2046<br>Cell: 012 584 3710<br>Fax: 03 7781 2047<br>info@harrowmerefreight.com<br>www.harrowmerefreight.com</p>
  <p class="address">48 Jalan Ampang<br>Kuala Lumpur 50450</p>
  <svg class="band" width="171" height="6" viewBox="0 0 171 6">
    <polygon points="0,1 110,1 106,4 0,4" fill="#8a8a8a"/>
    <polygon points="113,0 171,0 171,6 0,6 0,5 108,5" fill="#4f86c6"/>
  </svg>
</section>

<section class="sheet card-back" aria-label="Business card back">
  <div class="brand"><span class="dot"></span>Harrowmere Freight</div>
  <p class="slogan">QUICK, RELIABLE AND POLITE</p>
</section>

<section class="sheet slip" aria-label="Compliment slip">
  <div class="brand"><span class="dot"></span>Harrowmere Freight</div>
  <p class="addr small">B12 Kelana Square, Jalan SS7,<br>Petaling Jaya 47301</p>
  <svg class="band" width="416" height="14" viewBox="0 0 416 14">
    <defs>
      <linearGradient id="slGrey" x1="0" x2="1"><stop offset="0" stop-color="#555"/><stop offset="1" stop-color="#d0d0d0"/></linearGradient>
    </defs>
    <polygon points="0,2 284,2 278,10 0,10" fill="url(#slGrey)"/>
    <polygon points="288,0 416,0 416,14 0,14 0,11 280,11" fill="#4f86c6"/>
  </svg>
  <span class="band-url small">WWW.HARROWMEREFREIGHT.COM</span>
</section>

<section class="sheet envelope" aria-label="Envelope">
  <svg class="flap" width="416" height="60" viewBox="0 0 416 60">
    <defs>
      <linearGradient id="evBlue" x1="0" y1="0" x2="0" y2="1"><stop offset="0" stop-color="#4d7fc0"/><stop offset="1" stop-color="#5588c8"/></linearGradient>
    </defs>
    <path d="M0,0 H416 L400,52 Q398,58 392,58 H24 Q18,58 16,52 Z" fill="url(#evBlue)"/>
  </svg>
  <span class="flap-dot"></span>
  <p class="url">www.harrowmerefreight.com</p>
</section>

</body>
</html>
```